Climb Past Tuesday - Nobody Writes My Ending

The front book cover. The book will include life lessons I've learned through three breast cancer (Pink Ribbon) diagnoses and how to create positivity through adversity. Lessons that most people don't think of until they're hit with a life-altering setback. The chapters include Imposter Syndrome (Pink Ribbon Warriors don't have time to debate if they're good enough, they just jump in and get it done because life is too short), Stand Your Ground (stick up for your beliefs and advocate for yourself), The Flip Side of It's All About Me (like an emergency rescuer who must equip themselves first, you need to take care of yourself first). The main message in the book is when others say you CAN'T, I say you CAN! Warrior means being strong no matter what life deals you. I've included a word document with more information.
Updates

Please note: Pink is only to be an accent color. I'd like my brand colors to be included. The title of the book is to be the focus with an image to add to the book cover appeal.

Target Market(s)

professionals with a growth mindset and people going through adversity

Industry/Entity Type

HR, Libraries, Hosppitality,

Font styles to use
Sans Serif

Colors
6B429C
8869AF
B7A5CE
E3DAEB
F3F0F8

Requirements
Must have
• Be original. Cover to be appealing to male and female buyers. Incorporate my purple brand color. Be creative and unique.
Nice to have
• Although I have offered a suggestion, I'm open to a creative cover that wows me.
Should not have
• No cartoon image or stock image

```html
<!DOCTYPE html>
<html lang="en">
<head>
<meta charset="UTF-8">
<title>Climb Past Tuesday - Nobody Writes My Ending</title>
<link href="https://fonts.googleapis.com/css2?family=Jost:wght@400;500&display=swap" rel="stylesheet">
<style>
  :root {
    --surround: #262626;
    --paper: #ffffff;
    --title-deep: #3f2455;
    --title-bright: #64287c;
    --title-muted: #8e7490;
    --glove-light: #c65fd8;
    --glove-mid: #8a2a9a;
    --glove-edge: #f1eef3;
    --gold: #ebd57c;
    --ink: #111111;
  }
  html, body {
    margin: 0;
    padding: 0;
    width: 1200px;
    height: 1200px;
    overflow: hidden;
    background: var(--surround);
  }
  .cover {
    position: absolute;
    left: 228px;
    top: 16px;
    width: 704px;
    height: 1127px;
    background: var(--paper);
    font-family: "Jost", "Futura", sans-serif;
    overflow: hidden;
  }
  .title-line {
    position: absolute;
    left: 0;
    width: 100%;
    margin: 0;
    text-align: center;
    text-transform: uppercase;
    font-weight: 400;
    line-height: 1;
    white-space: nowrap;
  }
  .title-strong {
    background: linear-gradient(90deg, var(--title-deep), var(--title-bright));
    -webkit-background-clip: text;
    background-clip: text;
    color: transparent;
  }
  .title-soft { color: var(--title-muted); }
  .line-climb  { top: 58px;  font-size: 118px; letter-spacing: 1px; }
  .line-tuesday{ top: 196px; font-size: 136px; font-weight: 500; }
  .line-nobody { top: 360px; font-size: 78px; }
  .line-ending { top: 446px; font-size: 120px; }
  .hero-image {
    position: absolute;
    left: 0;
    top: 580px;
    width: 704px;
    height: 450px;
  }
  .subtitle {
    position: absolute;
    left: 250px;
    top: 712px;
    width: 240px;
    margin: 0;
    text-align: center;
    color: var(--gold);
    font-size: 28px;
    line-height: 31px;
    text-transform: uppercase;
    font-weight: 400;
  }
  .author {
    position: absolute;
    left: 0;
    top: 1056px;
    width: 100%;
    margin: 0;
    text-align: center;
    color: var(--ink);
    font-size: 33px;
    font-weight: 400;
  }
</style>
</head>
<body>
  <main class="cover">
    <h1 class="title">
      <span class="title-line title-strong line-climb">Climb Past</span>
      <span class="title-line title-strong line-tuesday">Tuesday</span>
      <span class="title-line title-soft line-nobody">Nobody Writes</span>
      <span class="title-line title-soft line-ending">My Ending</span>
    </h1>

    <svg class="hero-image" viewBox="0 0 704 450" role="img" aria-label="Purple boxing glove punching through torn white paper">
      <defs>
        <radialGradient id="paperShade" cx="50%" cy="45%" r="55%">
          <stop offset="0%" stop-color="#d9d6da"/>
          <stop offset="100%" stop-color="#ffffff"/>
        </radialGradient>
        <radialGradient id="gloveTone" cx="65%" cy="45%" r="60%">
          <stop offset="0%" stop-color="var(--glove-light)"/>
          <stop offset="100%" stop-color="var(--glove-mid)"/>
        </radialGradient>
      </defs>
      <rect width="704" height="450" fill="url(#paperShade)"/>
      <ellipse cx="340" cy="230" rx="210" ry="150" fill="url(#gloveTone)"/>
    </svg>

    <h2 class="subtitle">Life<br>Lessons<br>From<br>A 3X Pink<br>Warrior</h2>

    <p class="author">Rae Donnelly, CCMS, MCVP, CSP</p>
  </main>
</body>
</html>
```